Emerging Ed-Tech Startup seeking Stationery Designs!

We are in need of basic set of stationery designs to be used for our business operations, letters, emails, and in-office materials. We are a technology startup enhancing on campus work experience offerings by establishing a collaborative work environment for the completion of such tasks.

Our colors are Vibrant Tiffany Blue/Black/White.

Website: www.campusnorthway.com (Still under construction aside from the landing pages)

Please make sure the designs use a brighter more vibrant tiffany blue color than seen in the image files uploaded. We are not using those materials.

Our logo has been added as a file as well, please use that for any designs (include that logo). Thank you.

```html
<!DOCTYPE html>
<html lang="en">
<head>
<meta charset="utf-8">
<title>CampusNorthway Letterhead</title>
<link rel="stylesheet" href="https://fonts.googleapis.com/css2?family=Arimo:wght@400&family=Josefin+Sans:wght@400&display=swap">
<style>
  :root {
    --paper: #ffffff;
    --frame: #3a3a3a;
    --ink: #6b6b6b;
    --brand-ink: #2b2b2b;
    --tiffany: #3fc6d6;
    --tiffany-pale: #d9eef3;
    --slate: #6d6e70;
  }
  html, body {
    margin: 0;
    padding: 0;
    overflow: hidden;
    background: var(--paper);
  }
  .letterhead {
    position: relative;
    width: 864px;
    height: 1200px;
    background: var(--paper);
    overflow: hidden;
  }
  .page-frame {
    position: absolute;
    left: 11px;
    top: 0;
    width: 836px;
    height: 1196px;
    border: 1px solid var(--frame);
    box-sizing: border-box;
  }
  .brand {
    position: absolute;
    left: 78px;
    top: 84px;
    display: flex;
    align-items: center;
    gap: 14px;
  }
  .brand-mark {
    width: 22px;
    height: 22px;
    background: var(--tiffany);
  }
  .brand-name {
    font-family: "Josefin Sans", sans-serif;
    font-weight: 400;
    font-size: 23px;
    letter-spacing: 0.5px;
    color: var(--brand-ink);
  }
  .contact-line {
    position: absolute;
    left: 81px;
    top: 1010px;
    margin: 0;
    font-family: "Arimo", Arial, sans-serif;
    font-size: 10px;
    color: var(--ink);
    white-space: nowrap;
  }
  .contact-line .sep { padding: 0 6px; }
  .contact-line .web { color: var(--tiffany); }
  .corner-decoration {
    position: absolute;
    left: 12px;
    top: 848px;
    width: 835px;
    height: 348px;
    background: linear-gradient(100deg, var(--tiffany-pale) 0%, #b9dfe6 45%, var(--tiffany) 75%, var(--slate) 100%);
    clip-path: polygon(0 66%, 68% 66%, 100% 0, 100% 100%, 0 100%);
  }
</style>
</head>
<body>
<main class="letterhead">
  <div class="corner-decoration" role="img" aria-label="Decorative geometric corner shapes in tiffany blue and grey"></div>
  <div class="page-frame"></div>

  <header class="brand">
    <span class="brand-mark"></span>
    <span class="brand-name">CampusNorthway</span>
  </header>

  <p class="contact-line">
    House # B-14<span class="sep">|</span>Park Lane<span class="sep">|</span>+91 40 5182274<span class="sep">|</span>info@campusnorthway.com<span class="sep">|</span><span class="web">www.campusnorthway.com</span>
  </p>
</main>
</body>
</html>
```